Webdesign für Hunde- und Katzenernährungsberatung
Zielgruppe
Hunde und Katzenernährungsberatung, für Menschen, die auch bei ihren Hunden und Katzen auf gesunde, natürliche Ernährung achten wollen, ohne unnötigen Geschmacksverstärker, Zucker, Zusatzstoffe, etc. die gesundheitliche Probleme bei den Tieren verursachen können.
Umstellung auf natürliche, artgerechte Fütterung, teils roh, teils gekocht, angepasst auf Grösse, Rasse, Alter etc., auch speziell für Welpen
Beratung bei:
Übergewicht
Allergien
Unverträglichkeiten
Magen-Darm Problemen
individuelle Ernährungspläne
Selbsthergestellte Kekse, Leckerlies, Snacks, Pralinen und div. Hausmannskost in Einmachgläsern (alles auf Vorbestellung).
Diverse Accessoires
Halsbänder, Leinen, Geschirr aus div. natürlichen Materialien
Lern- und Spielzeug aus Holz und Stoff
div. Zubehör für Tiere, sowie auch für Frauchen und Herrchen
Aufgabenstellung
Die Seite sollte stilvoll aber nicht überfüllt sein und im Retro/Vintage Stil gehalten werden, da das Logo bereits sehr wirksam und eher auffällig ist, dezente Töne im Hintergrund, die Nahrungsmittel werden dann ev. auf Schieferplatten oder unauffälligem Hintergrund platziert. Ich sollte zu einem späteren Zeitpunkt selber Fotos, Links, Texte, etc. einfach dazu fügen können.

```html
<!DOCTYPE html>
<html lang="de">
<head>
<meta charset="utf-8">
<title>Napfglück – Ernährungsberatung für Hund und Katze</title>
<link href="https://fonts.googleapis.com/css2?family=Kaushan+Script&family=Open+Sans:wght@400;600;700;800&display=swap" rel="stylesheet">
<style>
:root{
  --orange:#c8731e;
  --orange-light:#f2b879;
  --blue:#8fbcd8;
  --blue-dark:#6f98b3;
  --paper:#f7f7f6;
  --white:#ffffff;
  --text:#6b6b6b;
  --ink:#3d3d3d;
  --stage:#e4e4e4;
}
*{box-sizing:border-box;margin:0;padding:0}
html,body{width:1200px;height:3000px;overflow:hidden}
body{background:var(--stage);font-family:"Open Sans",Arial,sans-serif;color:var(--text);position:relative}
.page{position:absolute;left:156px;top:0;width:888px;height:3000px;background:var(--paper);overflow:hidden}
.abs{position:absolute}
.script{font-family:"Kaushan Script",cursive;color:var(--orange);font-weight:400}
.copy{font-size:7px;line-height:11.5px;color:var(--text)}
.btn{position:absolute;height:17px;font-size:6.5px;font-weight:700;color:#fff;text-transform:uppercase;display:flex;align-items:center;justify-content:center;letter-spacing:.2px}
.btn--blue{background:var(--blue-dark)}
.btn--orange{background:var(--orange)}
.photo{position:absolute}

/* header */
.topbar{left:0;top:0;width:888px;height:47px;background:var(--white);box-shadow:0 2px 4px rgba(0,0,0,.08)}
.topbar::before{content:"";position:absolute;left:0;top:0;width:100%;height:3px;background:var(--blue)}
.brand-tab{left:170px;top:0;width:111px;height:78px;background:var(--white);border-radius:0 0 55px 55px;box-shadow:0 3px 5px rgba(0,0,0,.08);display:flex;flex-direction:column;align-items:center;justify-content:center;gap:5px}
.brand-tab .dot{width:34px;height:34px;border-radius:50%;background:var(--blue)}
.brand-name{font-weight:800;color:var(--blue-dark);font-size:11px;letter-spacing:.5px}
.nav{right:186px;top:20px;display:flex;gap:4px;font-size:7px;font-weight:700;text-transform:uppercase;color:var(--ink)}
.nav span.sep{color:#bbb}
.nav .active{color:var(--orange)}

/* hero */
.hero{left:0;top:47px;width:888px;height:287px;background:var(--paper);border-bottom:3px solid var(--orange-light)}
.arrow{top:128px;width:14px;height:20px}
.hero-title{left:190px;top:80px;width:250px;font-size:38px;line-height:34px;text-align:center}
.hero-sub{left:190px;top:158px;width:250px;text-align:center;font-size:6.5px;font-weight:600;color:var(--ink);text-transform:uppercase}
.hero-rule{left:230px;top:172px;width:170px;height:2px;background:var(--orange)}
.hero-rule.top{top:75px}
.hero-mark{left:455px;top:20px;width:250px;height:260px;display:flex;flex-direction:column;align-items:center;justify-content:center;gap:12px}
.hero-mark .circle{width:180px;height:180px;border-radius:50%;background:var(--blue)}
.hero-mark .brand-name{font-size:30px;letter-spacing:2px}

/* welcome */
.section-title{font-size:24px;line-height:24px}
.topics{font-size:8.5px;font-weight:600;color:var(--ink);line-height:15px;text-transform:uppercase}
.topics b{color:var(--orange);font-weight:700;padding:0 2px}

/* bands */
.blue-band{background:var(--blue)}
.band-title{color:#fff}
.ticks{list-style:none;font-size:6.5px;font-weight:700;color:#fff;text-transform:uppercase;line-height:12px}
.ticks li{display:flex;align-items:center;gap:5px}
.links-list{font-size:6.5px;font-weight:700;color:var(--orange);text-transform:uppercase;line-height:11.5px}

/* shop */
.filters{left:0;width:888px;text-align:center;font-size:6.5px;font-weight:700;color:#fff;text-transform:uppercase}
.filters span{padding:0 4px}
.filters .sep{color:#e9f2f8}
.card{position:absolute;width:119px;height:194px;background:#fff;box-shadow:0 2px 4px rgba(0,0,0,.15);text-align:center;padding:6px 6px 0}
.card .food{height:58px;background:linear-gradient(180deg,#d79a5e,#b46a2e);margin:0 10px}
.card .name{font-size:6px;font-weight:800;color:var(--orange);margin-top:8px;text-transform:uppercase}
.card .desc{font-size:5px;line-height:7.5px;color:var(--text);margin-top:4px;padding-bottom:4px;border-bottom:1px dotted var(--orange)}
.card .price{font-size:20px;font-weight:800;color:var(--orange);line-height:22px;margin-top:2px}
.card .tax{font-size:4.8px;color:var(--text);line-height:6.5px}
.card .tax em{font-style:normal;color:var(--orange)}
.card .btn{left:12px;width:95px;bottom:-4px;height:15px;font-size:5.8px}

/* newsletter */
.newsletter{left:0;top:2685px;width:888px;height:37px;background:var(--blue-dark)}
.news-input{left:186px;top:10px;width:160px;height:17px;background:#fff;font-size:6px;color:#aaa;padding:5px 6px}
.news-text{left:362px;top:8px;color:#fff;font-size:10px}
.news-text small{display:block;font-size:5.5px;color:#e6eef4}
.news-btn{left:626px;top:10px;width:75px;height:17px;background:#fff;color:var(--blue-dark);font-size:6px;font-weight:700;display:flex;align-items:center;justify-content:center;text-transform:uppercase}

/* contact */
.foot-brand{left:186px;top:2740px;display:flex;flex-direction:column;align-items:center;width:80px;gap:6px}
.foot-brand .dot{width:54px;height:54px;border-radius:50%;background:var(--blue)}
.address{left:186px;top:2843px;font-size:5.5px;line-height:8.5px;color:var(--ink)}
.address a{color:var(--orange);text-decoration:none;font-weight:600}
.socials{left:186px;top:2930px;display:flex;gap:14px}
.socials span{width:13px;height:13px;background:#8a8a8a;border-radius:3px}
.form-title{left:362px;top:2750px;font-size:22px}
.form-sub{left:362px;top:2780px;font-size:5.5px;color:var(--ink)}
.field{position:absolute;border-bottom:1px solid #ccc;font-size:5.5px;color:#999;text-transform:uppercase;height:14px}
.field.focus{border-bottom:1px solid var(--orange);color:var(--orange)}
.copy-check{left:362px;top:2928px;font-size:5.5px;color:var(--ink);display:flex;align-items:center;gap:4px}
.copy-check i{width:5px;height:5px;background:#999;display:inline-block}
.footerbar{left:0;top:2976px;width:888px;height:24px;background:var(--blue-dark);font-size:5.5px;color:#fff;display:flex;align-items:center;justify-content:space-between;padding:0 186px}
</style>
</head>
<body>
<div class="page">

  <header class="abs topbar">
    <nav class="abs nav">
      <span class="active">Startseite</span><span class="sep">·</span>
      <span>Ernährungsberatung</span><span class="sep">·</span>
      <span>Futter</span><span class="sep">·</span>
      <span>Accessories</span><span class="sep">·</span>
      <span>Onlineshop</span><span class="sep">·</span>
      <span>Kontakt</span>
    </nav>
  </header>
  <div class="abs brand-tab"><span class="dot"></span><span class="brand-name">NAPFGLÜCK</span></div>

  <section class="abs hero">
    <svg class="abs arrow" style="left:14px" viewBox="0 0 14 20"><path d="M11 2 L3 10 L11 18" fill="none" stroke="var(--blue-dark)" stroke-width="3"/></svg>
    <svg class="abs arrow" style="right:14px" viewBox="0 0 14 20"><path d="M3 2 L11 10 L3 18" fill="none" stroke="var(--blue-dark)" stroke-width="3"/></svg>
    <div class="abs hero-rule top"></div>
    <h1 class="abs script hero-title">Lorem ipsum dolor sit amet</h1>
    <p class="abs hero-sub">Lorem ipsum dolor sit amet consectetur adipiscing elit</p>
    <div class="abs hero-rule"></div>
    <div class="btn btn--blue" style="left:267px;top:199px;width:91px">Online Shop</div>
    <div class="abs hero-mark"><span class="circle"></span><span class="brand-name">NAPFGLÜCK</span></div>
  </section>

  <section>
    <div class="photo" role="img" aria-label="Porträtfoto der Ernährungsberaterin" style="left:164px;top:350px;width:216px;height:302px;background:linear-gradient(180deg,#d6c8b8 0%,#8f9199 100%)"></div>
    <h2 class="abs script section-title" style="left:407px;top:398px">Willkommen auf<br>unserer Website</h2>
    <p class="abs copy" style="left:407px;top:452px;width:255px">Lorem ipsum dolor sit amet, consectetur adipiscing elit, sed do eiusmod tempor incididunt ut labore et dolore magna aliqua. Ut enim ad minim veniam, quis nostrud exercitation ullamco laboris nisi ut aliquip ex ea commodo consequat. Duis aute irure dolor in reprehenderit in voluptate velit esse cillum dolore eu fugiat nulla pariatur.</p>
    <h3 class="abs script" style="left:407px;top:516px;font-size:17px">Beratung bei:</h3>
    <p class="abs topics" style="left:407px;top:542px;width:340px">Übergewicht <b>|</b> Allergien <b>|</b> Unverträglichkeiten<br>Magen-Darm Problemen <b>|</b> Individuelle Ernährungspläne</p>
    <p class="abs copy" style="left:407px;top:578px;width:255px">Lorem ipsum dolor sit amet, consectetur adipiscing elit, sed do eiusmod tempor incididunt ut labore et dolore magna aliqua. Ut enim ad minim veniam, quis nostrud exercitation ullamco laboris nisi ut aliquip ex ea commodo consequat.</p>
  </section>

  <section>
    <div class="photo" role="img" aria-label="Foto: Beagle frisst aus einem Metallnapf" style="left:456px;top:658px;width:432px;height:490px;background:linear-gradient(160deg,#b9804a 0%,#e8dfd4 100%)"></div>
    <div class="photo" role="img" aria-label="Foto: Katze frisst aus einem Metallnapf" style="left:0;top:920px;width:440px;height:228px;background:linear-gradient(160deg,#c2a585 0%,#e4ded7 100%)"></div>
    <h2 class="abs script section-title" style="left:186px;top:722px">Ernährungsberatung</h2>
    <p class="abs copy" style="left:186px;top:757px;width:255px">Lorem ipsum dolor sit amet, consectetur adipiscing elit, sed do eiusmod tempor incididunt ut labore et dolore magna aliqua. Ut enim ad minim veniam, quis nostrud exercitation ullamco laboris nisi ut aliquip ex ea commodo consequat. Duis aute irure dolor in reprehenderit in voluptate velit esse cillum dolore eu fugiat nulla pariatur.</p>
    <p class="abs copy" style="left:186px;top:827px;width:255px">Lorem ipsum dolor sit amet, consectetur adipiscing elit, sed do eiusmod tempor incididunt ut labore et dolore magna aliqua.</p>
    <div class="btn btn--orange" style="left:186px;top:867px;width:91px">Mehr Infos</div>
  </section>

  <section class="abs blue-band" style="left:0;top:1194px;width:888px;height:321px"></section>
  <div class="photo" role="img" aria-label="Foto: Chihuahua mit Napf im Maul und selbstgebackene Hundekekse" style="left:141px;top:1200px;width:280px;height:385px;background:linear-gradient(180deg,#d2b48c 0%,#b98a55 100%)"></div>
  <h2 class="abs script band-title section-title" style="left:450px;top:1246px;font-size:22px">Hausgemachte Tiernahrung</h2>
  <p class="abs copy" style="left:450px;top:1280px;width:255px;color:#fff">Lorem ipsum dolor sit amet, consectetur adipiscing elit, sed do eiusmod tempor incididunt ut labore et dolore magna aliqua. Ut enim ad minim veniam, quis nostrud exercitation ullamco laboris nisi ut aliquip ex ea commodo consequat. Duis aute irure dolor in reprehenderit in voluptate velit esse cillum dolore eu fugiat nulla pariatur.</p>
  <h3 class="abs script band-title" style="left:450px;top:1345px;font-size:15px">Sie können in unserem Online-Shop</h3>
  <ul class="abs ticks" style="left:455px;top:1370px">
    <li><svg width="8" height="6" viewBox="0 0 8 6"><path d="M1 3 L3 5 L7 1" fill="none" stroke="#fff" stroke-width="1.2"/></svg>Selbsthergestellte Kekse</li>
    <li><svg width="8" height="6" viewBox="0 0 8 6"><path d="M1 3 L3 5 L7 1" fill="none" stroke="#fff" stroke-width="1.2"/></svg>Leckerlies</li>
    <li><svg width="8" height="6" viewBox="0 0 8 6"><path d="M1 3 L3 5 L7 1" fill="none" stroke="#fff" stroke-width="1.2"/></svg>Snacks</li>
    <li><svg width="8" height="6" viewBox="0 0 8 6"><path d="M1 3 L3 5 L7 1" fill="none" stroke="#fff" stroke-width="1.2"/></svg>Pralinen</li>
    <li><svg width="8" height="6" viewBox="0 0 8 6"><path d="M1 3 L3 5 L7 1" fill="none" stroke="#fff" stroke-width="1.2"/></svg>Div. Hausmannskost in Einmachgläsern</li>
  </ul>
  <div class="btn btn--blue" style="left:450px;top:1441px;width:91px">Mehr Infos</div>

  <section>
    <h2 class="abs script section-title" style="left:186px;top:1596px">Zubehör</h2>
    <p class="abs copy" style="left:186px;top:1631px;width:255px">Lorem ipsum dolor sit amet, consectetur adipiscing elit, sed do eiusmod tempor incididunt ut labore et dolore magna aliqua. Ut enim ad minim veniam, quis nostrud exercitation ullamco laboris nisi ut aliquip ex ea commodo consequat. Duis aute irure dolor in reprehenderit in voluptate velit esse cillum dolore eu fugiat nulla pariatur.</p>
    <p class="abs copy" style="left:186px;top:1701px;width:255px">Lorem ipsum dolor sit amet, consectetur adipiscing elit, sed do eiusmod tempor incididunt ut labore et dolore magna aliqua.</p>
    <p class="abs links-list" style="left:186px;top:1731px">Halsbänder<br>Leinen<br>Geschirr aus div. natürlichen Materialien<br>Lern- und Spielzeug aus Holz und Stoff<br>Div. Zubehör für Tiere</p>
    <div class="btn btn--blue" style="left:186px;top:1802px;width:91px">Mehr Infos</div>
    <div class="photo" role="img" aria-label="Foto: Kätzchen neben einem Holz-Spielzeug mit Leckerlis" style="left:460px;top:1538px;width:390px;height:314px;background:linear-gradient(160deg,#d6b088 0%,#e9e2da 100%)"></div>
  </section>

  <section class="abs blue-band" style="left:0;top:1870px;width:888px;height:815px"></section>
  <h2 class="abs script band-title" style="left:0;width:888px;text-align:center;top:1892px;font-size:23px">Online Shop</h2>
  <p class="abs filters" style="top:1928px"><span>Alle Produkte</span><span class="sep">|</span><span>Food</span><span class="sep">|</span><span>Snacks</span><span class="sep">|</span><span>Pralinen</span><span class="sep">|</span><span>Zubehör</span></p>

  <article class="card" style="left:186px;top:1954px"><div class="food" role="img" aria-label="Produktfoto Trockenfutter"></div><p class="name">Produktname geht hier</p><p class="desc">Lorem ipsum dolor sit amet, consectetur adipiscing elit, sed do eiusmod tempor incididunt ut labore et dolore magna aliqua.</p><p class="price">€ 10,50</p><p class="tax">inkl. 19% MwSt. zzgl.<br><em>Versandkosten</em> | Lieferzeit 2 - 3 tage</p><div class="btn btn--orange">In den Warenkorb</div></article>
  <article class="card" style="left:318px;top:1954px"><div class="food" role="img" aria-label="Produktfoto Trockenfutter"></div><p class="name">Produktname geht hier</p><p class="desc">Lorem ipsum dolor sit amet, consectetur adipiscing elit, sed do eiusmod tempor incididunt ut labore et dolore magna aliqua.</p><p class="price">€ 10,50</p><p class="tax">inkl. 19% MwSt. zzgl.<br><em>Versandkosten</em> | Lieferzeit 2 - 3 tage</p><div class="btn btn--blue">In den Warenkorb</div></article>
  <article class="card" style="left:450px;top:1954px"><div class="food" role="img" aria-label="Produktfoto Trockenfutter"></div><p class="name">Produktname geht hier</p><p class="desc">Lorem ipsum dolor sit amet, consectetur adipiscing elit, sed do eiusmod tempor incididunt ut labore et dolore magna aliqua.</p><p class="price">€ 10,50</p><p class="tax">inkl. 19% MwSt. zzgl.<br><em>Versandkosten</em> | Lieferzeit 2 - 3 tage</p><div class="btn btn--blue">In den Warenkorb</div></article>
  <article class="card" style="left:583px;top:1954px"><div class="food" role="img" aria-label="Produktfoto Trockenfutter"></div><p class="name">Produktname geht hier</p><p class="desc">Lorem ipsum dolor sit amet, consectetur adipiscing elit, sed do eiusmod tempor incididunt ut labore et dolore magna aliqua.</p><p class="price">€ 10,50</p><p class="tax">inkl. 19% MwSt. zzgl.<br><em>Versandkosten</em> | Lieferzeit 2 - 3 tage</p><div class="btn btn--blue">In den Warenkorb</div></article>

  <article class="card" style="left:186px;top:2180px"><div class="food" role="img" aria-label="Produktfoto Trockenfutter"></div><p class="name">Produktname geht hier</p><p class="desc">Lorem ipsum dolor sit amet, consectetur adipiscing elit, sed do eiusmod tempor incididunt ut labore et dolore magna aliqua.</p><p class="price">€ 10,50</p><p class="tax">inkl. 19% MwSt. zzgl.<br><em>Versandkosten</em> | Lieferzeit 2 - 3 tage</p><div class="btn btn--blue">In den Warenkorb</div></article>
  <article class="card" style="left:318px;top:2180px"><div class="food" role="img" aria-label="Produktfoto Trockenfutter"></div><p class="name">Produktname geht hier</p><p class="desc">Lorem ipsum dolor sit amet, consectetur adipiscing elit, sed do eiusmod tempor incididunt ut labore et dolore magna aliqua.</p><p class="price">€ 10,50</p><p class="tax">inkl. 19% MwSt. zzgl.<br><em>Versandkosten</em> | Lieferzeit 2 - 3 tage</p><div class="btn btn--blue">In den Warenkorb</div></article>
  <article class="card" style="left:450px;top:2180px"><div class="food" role="img" aria-label="Produktfoto Trockenfutter"></div><p class="name">Produktname geht hier</p><p class="desc">Lorem ipsum dolor sit amet, consectetur adipiscing elit, sed do eiusmod tempor incididunt ut labore et dolore magna aliqua.</p><p class="price">€ 10,50</p><p class="tax">inkl. 19% MwSt. zzgl.<br><em>Versandkosten</em> | Lieferzeit 2 - 3 tage</p><div class="btn btn--blue">In den Warenkorb</div></article>
  <article class="card" style="left:583px;top:2180px"><div class="food" role="img" aria-label="Produktfoto Trockenfutter"></div><p class="name">Produktname geht hier</p><p class="desc">Lorem ipsum dolor sit amet, consectetur adipiscing elit, sed do eiusmod tempor incididunt ut labore et dolore magna aliqua.</p><p class="price">€ 10,50</p><p class="tax">inkl. 19% MwSt. zzgl.<br><em>Versandkosten</em> | Lieferzeit 2 - 3 tage</p><div class="btn btn--blue">In den Warenkorb</div></article>

  <article class="card" style="left:186px;top:2408px"><div class="food" role="img" aria-label="Produktfoto Trockenfutter"></div><p class="name">Produktname geht hier</p><p class="desc">Lorem ipsum dolor sit amet, consectetur adipiscing elit, sed do eiusmod tempor incididunt ut labore et dolore magna aliqua.</p><p class="price">€ 10,50</p><p class="tax">inkl. 19% MwSt. zzgl.<br><em>Versandkosten</em> | Lieferzeit 2 - 3 tage</p><div class="btn btn--blue">In den Warenkorb</div></article>
  <article class="card" style="left:318px;top:2408px"><div class="food" role="img" aria-label="Produktfoto Trockenfutter"></div><p class="name">Produktname geht hier</p><p class="desc">Lorem ipsum dolor sit amet, consectetur adipiscing elit, sed do eiusmod tempor incididunt ut labore et dolore magna aliqua.</p><p class="price">€ 10,50</p><p class="tax">inkl. 19% MwSt. zzgl.<br><em>Versandkosten</em> | Lieferzeit 2 - 3 tage</p><div class="btn btn--blue">In den Warenkorb</div></article>
  <article class="card" style="left:450px;top:2408px"><div class="food" role="img" aria-label="Produktfoto Trockenfutter"></div><p class="name">Produktname geht hier</p><p class="desc">Lorem ipsum dolor sit amet, consectetur adipiscing elit, sed do eiusmod tempor incididunt ut labore et dolore magna aliqua.</p><p class="price">€ 10,50</p><p class="tax">inkl. 19% MwSt. zzgl.<br><em>Versandkosten</em> | Lieferzeit 2 - 3 tage</p><div class="btn btn--blue">In den Warenkorb</div></article>
  <article class="card" style="left:583px;top:2408px"><div class="food" role="img" aria-label="Produktfoto Trockenfutter"></div><p class="name">Produktname geht hier</p><p class="desc">Lorem ipsum dolor sit amet, consectetur adipiscing elit, sed do eiusmod tempor incididunt ut labore et dolore magna aliqua.</p><p class="price">€ 10,50</p><p class="tax">inkl. 19% MwSt. zzgl.<br><em>Versandkosten</em> | Lieferzeit 2 - 3 tage</p><div class="btn btn--blue">In den Warenkorb</div></article>

  <div class="btn btn--blue" style="left:385px;top:2641px;width:119px">Zum Online-Shop</div>

  <section class="abs newsletter">
    <div class="abs news-input">Email</div>
    <p class="abs news-text">Newsletter anfordern und 5 Euro Gutschein sichern<small>Angebote &amp; Neuigkeiten direkt per E-Mail (Abmeldung jederzeit möglich)</small></p>
    <div class="abs news-btn">Jetzt anmelden</div>
  </section>

  <section>
    <div class="abs foot-brand"><span class="dot"></span><span class="brand-name" style="font-size:9px">NAPFGLÜCK</span></div>
    <p class="abs address">Company Address will be here<br>&nbsp;00112233 | Country Name will go here<br><br>Fon (0020) 123 44 567 · Fax (0020) 123 44 567<br><br><a>www.napfglueck.ch</a><br><a>info@napfglueck.ch</a></p>
    <div class="abs socials"><span></span><span style="background:var(--blue-dark)"></span><span></span><span></span><span></span></div>

    <h2 class="abs script form-title">Kontaktieren Sie uns jetzt</h2>
    <p class="abs form-sub">Sie können uns wie folgt erreichen. Wir freuen uns über Ihre Kontakt Anfrage.</p>
    <div class="field focus" style="left:362px;top:2797px;width:155px">Dein Name</div>
    <div class="field" style="left:537px;top:2797px;width:163px">Deine Email</div>
    <div class="field" style="left:362px;top:2824px;width:338px">Fach</div>
    <div class="field" style="left:362px;top:2852px;width:338px">Deine Nachricht</div>
    <div class="field" style="left:362px;top:2885px;width:338px"></div>
    <p class="abs copy-check">Kopie an sich selbst senden <i></i></p>
    <div class="btn btn--orange" style="left:612px;top:2920px;width:90px">Nachricht senden</div>
  </section>

  <footer class="abs footerbar">
    <span>© 2017 Napfglück · Alle Rechte vorbehalten</span>
    <span>Datenschutz &nbsp;|&nbsp; Impressum &nbsp;|&nbsp; AGB &nbsp;|&nbsp; Kontakt</span>
  </footer>
</div>
</body>
</html>
```